Quillmarsh Air Business Card Design

Design new, 2 sides, business cards for a residential and light commercial heating, air conditioning contractor.

Target Market(s)

Homeowners, small businesses

Industry/Entity Type

Business

Contact Information for Business Card

Dominic Westerhall
Phone - 862-415-2736
Email
Address - PO box 518
Brightwater NJ 07912
Website - www.HarborBreezeLLC.example

Requirements
Must have
• logo, company colors, standard size with no die cut, so I can use nova stamp

```html
<!DOCTYPE html>
<html lang="en">
<head>
<meta charset="utf-8">
<title>Quillmarsh Air Business Card</title>
<link href="https://fonts.googleapis.com/css2?family=Libre+Baskerville:wght@400;700&family=Arimo:wght@400&display=swap" rel="stylesheet">
<style>
  :root {
    --burgundy: #9e1f36;
    --burgundy-deep: #8a1a2f;
    --orange: #f08a1c;
    --ink-grey: #5a5a5a;
    --paper: #ffffff;
    --backdrop: #e9e7e3;
  }
  * { box-sizing: border-box; margin: 0; padding: 0; }
  html, body { width: 1200px; height: 950px; overflow: hidden; }
  body {
    background: var(--backdrop);
    font-family: "Arimo", Arial, sans-serif;
    position: relative;
  }
  .card {
    position: absolute;
    width: 630px;
    height: 360px;
    border-radius: 4px;
    box-shadow: 0 10px 24px rgba(0,0,0,0.22);
    overflow: hidden;
  }
  .card--front {
    left: 440px;
    top: 60px;
    background: var(--burgundy);
  }
  .card--back {
    left: 130px;
    top: 500px;
    background: var(--paper);
  }
  .brand-name {
    position: absolute;
    font-family: "Libre Baskerville", Georgia, serif;
    font-weight: 700;
    color: #ffffff;
    white-space: nowrap;
    display: flex;
    align-items: center;
    gap: 14px;
  }
  .brand-name .brand-dot {
    width: 14px; height: 14px; border-radius: 50%;
    background: var(--orange);
    flex: none;
  }
  .card--front .brand-name {
    left: 50%; top: 50%;
    transform: translate(-50%, -50%);
    font-size: 40px;
  }
  .band {
    position: absolute;
    left: 0; right: 0;
    top: 58px;
    height: 52px;
    background: var(--burgundy);
  }
  .card--back .brand-name {
    left: 50%; top: 84px;
    transform: translate(-50%, -50%);
    font-size: 30px;
    background: var(--burgundy-deep);
    padding: 14px 24px;
    border-radius: 4px;
  }
  .contact-list {
    position: absolute;
    left: 34px; top: 150px;
    list-style: none;
  }
  .contact-list li {
    display: flex;
    align-items: center;
    gap: 10px;
    font-size: 15px;
    color: var(--ink-grey);
    line-height: 24px;
  }
  .contact-list svg { width: 14px; height: 14px; flex: none; fill: var(--burgundy); }
  .signature {
    position: absolute;
    right: 40px; bottom: 36px;
    width: 250px;
  }
  .signature .person-name {
    font-family: "Libre Baskerville", Georgia, serif;
    color: var(--burgundy);
    font-size: 21px;
    letter-spacing: 0.5px;
  }
  .signature .person-title {
    font-family: "Libre Baskerville", Georgia, serif;
    color: var(--orange);
    font-size: 15px;
    letter-spacing: 1px;
    margin-bottom: 6px;
  }
  .signature .address {
    color: var(--ink-grey);
    font-size: 15px;
    line-height: 22px;
    font-style: normal;
  }
</style>
</head>
<body>

  <section class="card card--front" aria-label="Card front">
    <div class="brand-name"><span class="brand-dot"></span>Quillmarsh Air</div>
  </section>

  <section class="card card--back" aria-label="Card back">
    <div class="band"></div>
    <div class="brand-name"><span class="brand-dot"></span>Quillmarsh Air</div>

    <ul class="contact-list">
      <li>
        <svg viewBox="0 0 16 16" aria-hidden="true"><path d="M3 1h3l1.5 4-2 1.3a9 9 0 0 0 4.2 4.2L11 8.5 15 10v3a2 2 0 0 1-2 2A12 12 0 0 1 1 3a2 2 0 0 1 2-2z"/></svg>
        973 514 2287
      </li>
      <li>
        <svg viewBox="0 0 16 16" aria-hidden="true"><path d="M4 0h8a1 1 0 0 1 1 1v14a1 1 0 0 1-1 1H4a1 1 0 0 1-1-1V1a1 1 0 0 1 1-1zm1 2v10h6V2zm3 11a1 1 0 1 0 0 2 1 1 0 0 0 0-2z"/></svg>
        973 608 4419
      </li>
      <li>
        <svg viewBox="0 0 16 16" aria-hidden="true"><path d="M4 1h6v4H4zM2 6h12a1 1 0 0 1 1 1v7a1 1 0 0 1-1 1H2a1 1 0 0 1-1-1V7a1 1 0 0 1 1-1zm2 3v2h8V9z"/></svg>
        973 722 0356
      </li>
      <li>
        <svg viewBox="0 0 16 16" aria-hidden="true"><path d="M1 3h14v10H1zm1.5 1.5L8 9l5.5-4.5z"/></svg>
        marcus@quillmarshair.example
      </li>
      <li>
        <svg viewBox="0 0 16 16" aria-hidden="true"><path d="M8 0a5.5 5.5 0 0 1 5.5 5.5C13.5 10 8 16 8 16S2.5 10 2.5 5.5A5.5 5.5 0 0 1 8 0zm0 3.5a2 2 0 1 0 0 4 2 2 0 0 0 0-4z"/></svg>
        www.quillmarshair.example
      </li>
    </ul>

    <div class="signature">
      <p class="person-name">MARCUS HOLLIN</p>
      <p class="person-title">PRESIDENT</p>
      <address class="address">4127 Linden Court<br>Ashford, NJ 07930</address>
    </div>
  </section>

</body>
</html>
```